Tall ridge firewood

It a new firewood outlet in Ridgevale NSW that will only sell top hardwood firewood (ironbark , red gum, grey gum, an box mix. I would like to see a web page the we can do order online payment for delivery. It will all so need to have photos of the firewood. I all so have logo for tall ridge firewood
Must have a modem look but easy to use I would like to see a black back ground of some sort.

Here are some other firewood web pages for ideas and firewood info
http://www.example-logpile.com.au
http://www.example-stackwood.com.au
http://www.example-splitlog.com.au
http://www.example-kendaltimber.com.au/firewood

Industry/Entity Type

Firewood

```html
<!DOCTYPE html>
<html lang="en">
<head>
<meta charset="utf-8">
<title>Tall Ridge Firewood</title>
<link rel="stylesheet" href="https://fonts.googleapis.com/css2?family=Roboto+Condensed:wght@400;700&family=Arimo:wght@400;700&display=swap">
<style>
:root{
  --brand-blue:#1a74bd;
  --nav-blue:#2f8fdd;
  --heading-blue:#1e6fb8;
  --order-orange:#f26419;
  --dark:#1b1b1b;
  --nav-active:#2a2a2a;
  --text:#666;
  --text-dark:#333;
  --tile-grey:#efefef;
  --footer-grey:#f2f2f2;
  --line:#dcdcdc;
  --white:#fff;
}
*{margin:0;padding:0;box-sizing:border-box}
html,body{width:1038px;height:1200px;overflow:hidden;background:var(--white)}
body{position:relative;font-family:"Arimo",Arial,sans-serif;color:var(--text)}
.abs{position:absolute}
h2,h3{font-weight:400}

/* header */
.site-header{left:0;top:0;width:1038px;height:177px;background:var(--brand-blue)}
.brand{left:140px;top:0;width:186px;height:157px;background:var(--white);display:flex;flex-direction:column;align-items:center;justify-content:center;gap:10px}
.brand-dot{width:58px;height:58px;border-radius:50%;background:var(--brand-blue)}
.brand-name{font-family:"Roboto Condensed",Arial,sans-serif;font-weight:700;font-size:17px;color:var(--brand-blue);letter-spacing:.3px}
.call{left:522px;top:62px;color:var(--white)}
.call-label{font-size:12px;color:#cfe3f4}
.call-number{font-size:20px;font-weight:700;margin-top:2px;letter-spacing:.3px}
.address{left:717px;top:62px;font-size:11.5px;line-height:13px;color:var(--white)}
.address .muted{color:#cfe3f4}
.address u{color:var(--white)}

/* nav */
.nav-band{left:0;top:177px;width:1038px;height:29px;background:var(--nav-blue)}
.main-nav{left:139px;top:177px;height:29px;display:flex}
.main-nav a{display:flex;align-items:center;justify-content:center;height:29px;font-family:"Roboto Condensed",Arial,sans-serif;font-size:11.5px;color:var(--white);text-decoration:none;border-right:1px solid #4aa0e4}
.main-nav a.active{background:var(--nav-active);border-right:none}
.main-nav a.order{background:var(--order-orange);font-weight:700;border-right:none}

/* hero */
.hero-bg{left:0;top:206px;width:1038px;height:352px;background:linear-gradient(90deg,#151515,#2a2a2a 8%,#171717 14%,#111 86%,#2a2a2a 93%,#141414)}
.hero-photo{left:139px;top:206px;width:760px;height:352px;background:radial-gradient(ellipse at 52% 60%,#ffcc4a 0%,#f08a1c 18%,#8a3a12 38%,#4a3128 60%,#2a211d 85%)}
.hero-arrow{width:30px;height:24px;background:var(--white);display:flex;align-items:center;justify-content:center;top:370px}
.hero-caption{left:385px;top:366px;width:268px;height:32px;background:var(--brand-blue);border:1px solid #6fb1e8;color:var(--white);font-size:17px;display:flex;align-items:center;justify-content:center;letter-spacing:.2px}

/* products */
.product{top:583px;width:156px;height:161px}
.product-photo{width:156px;height:118px}
.product-label{height:43px;background:var(--tile-grey);display:flex;align-items:center;justify-content:center;font-family:"Roboto Condensed",Arial,sans-serif;font-size:16px;color:var(--text-dark)}
.product.featured .product-label{background:var(--brand-blue);color:var(--white)}

/* info columns */
.col-title{font-family:"Roboto Condensed",Arial,sans-serif;font-weight:400;font-size:21px;color:var(--heading-blue);top:791px}
.body-text{font-size:10px;line-height:12px;color:var(--text)}
.divider{top:792px;width:1px;height:186px;background:var(--line)}
.list-row{display:flex;align-items:flex-start;height:38px}
.tick{width:12px;margin-right:10px;margin-top:2px}
.news-num{font-family:"Roboto Condensed",Arial,sans-serif;font-weight:700;font-size:19px;color:var(--dark);width:31px;line-height:18px}
.btn-dark{top:957px;height:21px;padding:0 11px;background:linear-gradient(#3a3a3a,#111);color:var(--white);font-size:9.5px;display:flex;align-items:center;border:1px solid #000}

/* footer */
.site-footer{left:0;top:1011px;width:1038px;height:161px;background:var(--footer-grey)}
.foot-title{font-size:9.5px;font-weight:700;color:var(--heading-blue);top:1030px}
.foot-links{top:1051px;list-style:none;font-size:9.5px;line-height:13.7px;color:#555}
.foot-links li::before{content:"»";margin-right:6px;color:#777}
.card{width:30px;height:20px;border-radius:2px}
.social{width:23px;height:23px}
.client-title{left:654px;top:1027px;font-family:"Roboto Condensed",Arial,sans-serif;font-weight:700;font-size:14px;color:var(--heading-blue)}
.btn-blue{left:655px;top:1126px;width:75px;height:21px;background:var(--nav-blue);color:var(--white);font-size:9.5px;display:flex;align-items:center;justify-content:center}
.copyright{left:0;top:1172px;width:1038px;height:28px;background:var(--dark);color:var(--white);font-size:9.5px;display:flex;align-items:center;justify-content:center}
</style>
</head>
<body>

<header class="abs site-header"></header>
<div class="abs brand">
  <div class="brand-dot"></div>
  <div class="brand-name">TALL RIDGE FIREWOOD</div>
</div>
<div class="abs call">
  <div class="call-label">Call us</div>
  <div class="call-number">0400 318 275</div>
</div>
<div class="abs address">
  215, Lorem Ipsum is simply dummy<br>
  Ridgevale NSW<br>
  <span class="muted">Email - </span><u>info@tallridgefirewood.com</u>
</div>

<div class="abs nav-band"></div>
<nav class="abs main-nav">
  <a class="active" href="#" style="width:80px">HOME</a>
  <a href="#" style="width:89px">ABOUT US</a>
  <a href="#" style="width:90px">PRODUCTS</a>
  <a href="#" style="width:110px">ACCESSORIES</a>
  <a href="#" style="width:88px">DELIVERY</a>
  <a href="#" style="width:73px">FAQ`S</a>
  <a href="#" style="width:124px;border-right:none">CONTACT US</a>
  <a class="order" href="#" style="width:106px">ORDER ONLINE</a>
</nav>

<section>
  <div class="abs hero-bg" role="img" aria-label="Dark timber plank background"></div>
  <div class="abs hero-photo" role="img" aria-label="Photo of hardwood logs burning in a stone fireplace"></div>
  <div class="abs hero-arrow" style="left:139px">
    <svg width="10" height="14" viewBox="0 0 10 14"><path d="M8 1 2 7l6 6" fill="none" stroke="#1a74bd" stroke-width="3"/></svg>
  </div>
  <div class="abs hero-arrow" style="left:869px">
    <svg width="10" height="14" viewBox="0 0 10 14"><path d="m2 1 6 6-6 6" fill="none" stroke="#1a74bd" stroke-width="3"/></svg>
  </div>
  <div class="abs hero-caption">TOP&nbsp;<b>HARDWOOD</b>&nbsp;FIREWOOD</div>
</section>

<section>
  <div class="abs product featured" style="left:139px">
    <div class="product-photo" role="img" aria-label="Photo of split ironbark firewood" style="background:linear-gradient(135deg,#3a2414,#a8683a 45%,#5a3418)"></div>
    <div class="product-label">IRONBARK</div>
  </div>
  <div class="abs product" style="left:341px">
    <div class="product-photo" role="img" aria-label="Photo of stacked red gum firewood" style="background:linear-gradient(135deg,#8a4a38,#c98f78 50%,#7a3e2e)"></div>
    <div class="product-label">RED GUM</div>
  </div>
  <div class="abs product" style="left:542px">
    <div class="product-photo" role="img" aria-label="Photo of cut grey gum logs" style="background:linear-gradient(135deg,#5a5c5e,#9a9c98 50%,#4a4c4c)"></div>
    <div class="product-label">GREY GUM</div>
  </div>
  <div class="abs product" style="left:744px">
    <div class="product-photo" role="img" aria-label="Photo of box mix firewood burning in a fireplace" style="background:radial-gradient(ellipse at 55% 45%,#ffb53a,#a44c14 35%,#2a1f1a 75%)"></div>
    <div class="product-label">BOX MIX</div>
  </div>
</section>

<section>
  <h2 class="abs col-title" style="left:139px">WELCOME TO OUR SITE</h2>
  <div class="abs body-text" style="left:139px;top:832px;width:200px">
    <p>Lorem ipsum dolor sit amet, consectetur adipisicing elit, sed do eiusmod tempor incididunt ut labore et dolore magna aliqua. Ut enim ad minim veniam, quis nostrud exercitation ullamco.</p>
    <p style="margin-top:12px">Duis aute irure dolor in reprehenderit in voluptate velit esse cillum dolore eu fugiat nulla pariatur ...</p>
  </div>
  <a class="abs btn-dark" style="left:139px">READ MORE</a>

  <div class="abs divider" style="left:378px"></div>

  <h2 class="abs col-title" style="left:419px">WHY CHOOSE US?</h2>
  <div class="abs" style="left:420px;top:833px;width:220px">
    <div class="list-row"><svg class="tick" viewBox="0 0 12 10"><path d="m1 5 3.5 3.5L11 1.5" fill="none" stroke="#999" stroke-width="2"/></svg><span class="body-text">Lorem ipsum dolor sit amet, consectetur adipisicing elit.</span></div>
    <div class="list-row"><svg class="tick" viewBox="0 0 12 10"><path d="m1 5 3.5 3.5L11 1.5" fill="none" stroke="#999" stroke-width="2"/></svg><span class="body-text">Lorem ipsum dolor sit amet, consectetur adipisicing elit.</span></div>
    <div class="list-row"><svg class="tick" viewBox="0 0 12 10"><path d="m1 5 3.5 3.5L11 1.5" fill="none" stroke="#999" stroke-width="2"/></svg><span class="body-text">Lorem ipsum dolor sit amet, consectetur adipisicing elit.</span></div>
  </div>
  <a class="abs btn-dark" style="left:420px">READ MORE</a>

  <div class="abs divider" style="left:655px"></div>

  <h2 class="abs col-title" style="left:690px">LATEST NEWS</h2>
  <div class="abs" style="left:691px;top:833px;width:210px">
    <div class="list-row"><span class="news-num">01</span><span class="body-text">Lorem ipsum dolor sit amet, consectetur adipisicing elit.</span></div>
    <div class="list-row"><span class="news-num">02</span><span class="body-text">Lorem ipsum dolor sit amet, consectetur adipisicing elit.</span></div>
    <div class="list-row"><span class="news-num">03</span><span class="body-text">Lorem ipsum dolor sit amet, consectetur adipisicing elit.</span></div>
  </div>
  <a class="abs btn-dark" style="left:691px">VIEW ALL</a>
</section>

<footer class="abs site-footer"></footer>
<h3 class="abs foot-title" style="left:140px">NAVIGATION</h3>
<ul class="abs foot-links" style="left:140px">
  <li>Home</li><li>About Us</li><li>Products</li><li>Accessories</li><li>Contact Us</li>
</ul>
<h3 class="abs foot-title" style="left:283px;font-weight:400">ORDER ONLINE</h3>
<ul class="abs foot-links" style="left:283px">
  <li>Terms &amp; Conditions</li><li>Delivery</li><li>Faq`s</li>
</ul>
<h3 class="abs foot-title" style="left:453px">PAYMENT OPTION</h3>
<div class="abs" style="left:454px;top:1052px;display:flex;gap:10px">
  <div class="card" style="background:#2a4e9a"></div>
  <div class="card" style="background:#d8432c"></div>
  <div class="card" style="background:#e98a2a"></div>
</div>
<h3 class="abs foot-title" style="left:453px;top:1093px">FOLLOW US ON</h3>
<div class="abs" style="left:454px;top:1115px;display:flex;gap:4px">
  <div class="social" style="background:#3b5a98"></div>
  <div class="social" style="background:#2aa7df"></div>
  <div class="social" style="background:#1a7ab5"></div>
  <div class="social" style="background:#d9493a"></div>
</div>
<h3 class="abs client-title">Happy Client`s</h3>
<p class="abs body-text" style="left:654px;top:1050px;width:250px;line-height:12px">Lorem ipsum dolor sit amet, consectetur adipisicing elit, sed do eiusmod tempor incididunt ut labore et dolore magna aliqua.</p>
<p class="abs body-text" style="left:654px;top:1098px"><b style="color:#444">Sam</b>. 15/06/13</p>
<a class="abs btn-blue">READ MORE</a>

<div class="abs copyright">COPYRIGHT © TALL RIDGE FIREWOOD 2013. ALL RIGHT RESERVED.</div>

</body>
</html>
```